Fitness Business Card Design Needed

We are looking for a business card design that stands out but is also simple and unique. I like the idea of on one side using the picture of myself with my logo at my feet. I love the texture on the business card so please take that into account when designing. Then on the other side having my contact details. I want it to be clean, modern, and pretty. I am open to designs that allow spot gloss or gold foiling.

Contact Information for Business Card

Space for Name, Phone number, email, and website

```html
<!DOCTYPE html>
<html lang="en">
<head>
<meta charset="utf-8">
<title>Cedarpoint Training – Business Cards</title>
<link href="https://fonts.googleapis.com/css2?family=Montserrat:wght@300;400;500;700&display=swap" rel="stylesheet">
<style>
  :root {
    --backdrop: #e9e6e1;
    --card-light: #112536;
    --card-dark: #07111b;
    --gold: #d8a447;
    --brand-ink: #7d8a96;
    --ink: #f1efe9;
    --divider: #c9ced4;
  }
  html, body {
    margin: 0;
    width: 1200px;
    height: 1200px;
    overflow: hidden;
    background: var(--backdrop);
    font-family: "Montserrat", Arial, sans-serif;
  }
  .sheet {
    position: relative;
    width: 1200px;
    height: 1200px;
  }
  .card {
    position: absolute;
    left: 150px;
    width: 900px;
    height: 514px;
    background: radial-gradient(ellipse at 40% 45%, var(--card-light) 0%, var(--card-dark) 100%);
    box-shadow: 0 12px 30px rgba(0,0,0,0.28);
    overflow: hidden;
  }
  .card--contact { top: 56px; }
  .card--portrait { top: 630px; }

  .brand {
    position: absolute;
    display: flex;
    align-items: center;
    gap: 16px;
  }
  .brand__mark {
    width: 22px;
    height: 22px;
    border: 2px solid var(--gold);
    flex: none;
  }
  .brand__name {
    font-weight: 400;
    font-size: 28px;
    letter-spacing: 1px;
    color: var(--brand-ink);
    white-space: nowrap;
  }

  .card--contact .brand { left: 60px; top: 240px; }
  .card--contact .divider {
    position: absolute;
    left: 494px;
    top: 150px;
    width: 1px;
    height: 230px;
    background: var(--divider);
  }
  .contact {
    position: absolute;
    left: 540px;
    top: 150px;
  }
  .contact__name {
    margin: 0;
    font-weight: 700;
    font-size: 38px;
    color: var(--gold);
    letter-spacing: 0.5px;
  }
  .contact__role {
    margin: 2px 0 18px;
    font-size: 21px;
    font-weight: 400;
    color: var(--ink);
  }
  .contact__list {
    list-style: none;
    margin: 0;
    padding: 0;
  }
  .contact__item {
    display: flex;
    align-items: center;
    gap: 12px;
    font-size: 21px;
    color: var(--ink);
    line-height: 34px;
  }
  .contact__icon {
    width: 18px;
    height: 18px;
    flex: none;
  }

  .portrait {
    position: absolute;
    left: 40px;
    top: 30px;
    width: 300px;
    height: 454px;
    background: linear-gradient(180deg, #3a3f47 0%, #c9836b 35%, #d96a4b 55%, #b97a62 100%);
    border-radius: 150px 150px 20px 20px;
    opacity: 0.85;
  }
  .card--portrait .brand { left: 450px; top: 240px; }
</style>
</head>
<body>
<main class="sheet">

  <section class="card card--contact" aria-label="Business card, contact side">
    <div class="brand">
      <span class="brand__mark"></span>
      <span class="brand__name">CEDARPOINT TRAINING</span>
    </div>
    <div class="divider"></div>
    <div class="contact">
      <h1 class="contact__name">NADIA BROOKS</h1>
      <p class="contact__role">Manager</p>
      <ul class="contact__list">
        <li class="contact__item">
          <svg class="contact__icon" viewBox="0 0 18 18"><rect x="4" y="1" width="10" height="16" rx="2" fill="none" stroke="#d8a447" stroke-width="1.6"/><circle cx="9" cy="14" r="1" fill="#d8a447"/></svg>
          555-014-2290
        </li>
        <li class="contact__item">
          <svg class="contact__icon" viewBox="0 0 18 18"><path d="M4 2l3 3-2 2c1 2 3 4 5 5l2-2 3 3-2 3C8 15 3 10 2 4z" fill="#d8a447"/></svg>
          555-017-3381
        </li>
        <li class="contact__item">
          <svg class="contact__icon" viewBox="0 0 18 18"><rect x="1" y="3" width="16" height="12" fill="#d8a447"/><path d="M1 3l8 7 8-7" fill="none" stroke="#07111b" stroke-width="1.4"/></svg>
          hello@northvalefit.com
        </li>
        <li class="contact__item">
          <svg class="contact__icon" viewBox="0 0 18 18"><circle cx="9" cy="9" r="7.5" fill="none" stroke="#d8a447" stroke-width="1.5"/><ellipse cx="9" cy="9" rx="3.2" ry="7.5" fill="none" stroke="#d8a447" stroke-width="1.2"/><path d="M1.5 9h15M3 5h12M3 13h12" stroke="#d8a447" stroke-width="1.1"/></svg>
          www.northvalefit.com
        </li>
      </ul>
    </div>
  </section>

  <section class="card card--portrait" aria-label="Business card, portrait side">
    <div class="portrait" role="img" aria-label="Full-length photo of the trainer in a red two-piece, hands on hips, standing above the brand name"></div>
    <div class="brand">
      <span class="brand__mark"></span>
      <span class="brand__name">CEDARPOINT TRAINING</span>
    </div>
  </section>

</main>
</body>
</html>
```